Bramblewood Card Company Business Cards

We are a trading card store with Glimmorax, sports and other TCG cards, we need a business card design that encompasses a clean cut, modern style with a retro flare. website is bramblewoodcardco.com for reference. Can utilize a comic book era feel or a more modern outdoor feel to utilize the "Pacific Northwest" elements of tress, mountains, etc.

Industry/Entity Type

Trading cards and collectibles

Contact Information for Business Card

business name, email address, phone number, name, owner job title

Font styles to use
Sans Serif

```html
<!DOCTYPE html>
<html lang="en">
<head>
<meta charset="utf-8">
<title>Bramblewood Card Company – Business Cards</title>
<link rel="stylesheet" href="https://fonts.googleapis.com/css2?family=Montserrat:wght@400;600;700&family=Mulish:wght@400;600&display=swap">
<style>
  :root {
    --backdrop: #d6d9da;
    --card-white: #f7f7f6;
    --brand-teal: #12b6da;
    --brand-teal-deep: #0d9fc0;
    --ink: #2f2f31;
    --ink-soft: #444446;
    --watermark: #ececeb;
  }
  * { box-sizing: border-box; margin: 0; padding: 0; }
  html, body { width: 1200px; height: 829px; overflow: hidden; }
  body {
    background: var(--backdrop);
    display: flex;
    align-items: center;
    justify-content: center;
    gap: 40px;
    font-family: "Mulish", "Helvetica Neue", Arial, sans-serif;
  }
  .card {
    position: relative;
    width: 540px;
    height: 309px;
    border-radius: 3px;
    overflow: hidden;
    box-shadow: 0 10px 24px rgba(0,0,0,.12);
  }

  /* Front */
  .card--front {
    background: var(--card-white);
    border-bottom: 4px solid var(--brand-teal);
  }
  .front__brand {
    position: absolute;
    top: 34px;
    left: 38px;
    display: flex;
    align-items: center;
    gap: 10px;
    font-family: "Montserrat", Arial, sans-serif;
    font-weight: 700;
    font-size: 15px;
    letter-spacing: .06em;
    text-transform: uppercase;
    color: var(--ink);
    line-height: 1.2;
  }
  .front__brand-mark {
    width: 14px; height: 14px;
    background: var(--brand-teal);
    flex: none;
  }
  .front__watermark {
    position: absolute;
    right: 30px;
    bottom: 24px;
    font-family: "Montserrat", Arial, sans-serif;
    font-weight: 700;
    font-size: 34px;
    letter-spacing: .04em;
    text-transform: uppercase;
    color: var(--watermark);
    line-height: 1;
  }
  .contact {
    position: absolute;
    left: 38px;
    top: 108px;
    font-size: 13.5px;
    color: var(--ink-soft);
    line-height: 1.55;
    list-style: none;
  }
  .contact__address { margin-bottom: 4px; }
  .contact__item { display: flex; align-items: center; gap: 8px; }
  .contact__icon { width: 11px; height: 11px; flex: none; fill: var(--brand-teal); }
  .person {
    position: absolute;
    right: 48px;
    top: 140px;
    text-align: right;
  }
  .person__name {
    font-family: "Montserrat", Arial, sans-serif;
    font-weight: 700;
    font-size: 22px;
    letter-spacing: .05em;
    color: var(--brand-teal);
    text-transform: uppercase;
  }
  .person__title {
    font-size: 14px;
    color: var(--ink-soft);
    margin-top: 2px;
  }
  .person__tab {
    position: absolute;
    right: 0;
    top: 148px;
    width: 22px;
    height: 30px;
    background: var(--brand-teal);
  }

  /* Back */
  .card--back {
    background: var(--brand-teal);
    border-bottom: 4px solid var(--brand-teal-deep);
    display: flex;
    align-items: center;
    justify-content: center;
  }
  .back__brand {
    display: flex;
    align-items: center;
    gap: 14px;
    font-family: "Montserrat", Arial, sans-serif;
    font-weight: 700;
    font-size: 24px;
    letter-spacing: .06em;
    text-transform: uppercase;
    color: var(--ink);
    line-height: 1.2;
  }
  .back__brand-mark {
    width: 22px; height: 22px;
    border-radius: 50%;
    background: var(--ink);
    flex: none;
  }
</style>
</head>
<body>
  <section class="card card--front" aria-label="Business card front">
    <div class="front__brand"><span class="front__brand-mark"></span>Bramblewood<br>Card Company</div>

    <ul class="contact">
      <li class="contact__address">P.O. Box 7308 Fernline Road<br>Cedar Falls WA 9187</li>
      <li class="contact__item">
        <svg class="contact__icon" viewBox="0 0 12 12" aria-hidden="true"><path d="M2.5 1 4.5 1 5.3 3.6 4 4.6C4.6 6 6 7.4 7.4 8L8.4 6.7 11 7.5 11 9.5C11 10.3 10.3 11 9.5 11 5 11 1 7 1 2.5 1 1.7 1.7 1 2.5 1Z"/></svg>
        (555) 014 2267
      </li>
      <li class="contact__item">
        <svg class="contact__icon" viewBox="0 0 12 12" aria-hidden="true"><path d="M1 2.5h10v7H1z M1 2.5l5 4 5-4" fill="none" stroke="#12b6da" stroke-width="1.3"/></svg>
        info@bramblewoodcardco.com
      </li>
      <li class="contact__item">
        <svg class="contact__icon" viewBox="0 0 12 12" aria-hidden="true"><g fill="none" stroke="#12b6da" stroke-width="1.1"><circle cx="6" cy="6" r="5"/><ellipse cx="6" cy="6" rx="2.2" ry="5"/><path d="M1 6h10"/></g></svg>
        www.bramblewoodcardco.com
      </li>
    </ul>

    <div class="person">
      <p class="person__name">Dorian Hale</p>
      <p class="person__title">CEO/Founder</p>
    </div>
    <span class="person__tab" aria-hidden="true"></span>

    <div class="front__watermark" aria-hidden="true">Bramblewood</div>
  </section>

  <section class="card card--back" aria-label="Business card back">
    <div class="back__brand"><span class="back__brand-mark"></span>Bramblewood<br>Card Company</div>
  </section>
</body>
</html>
```